Marwick Law Letterhead

We need a new letterhead design for a Law Firm. The address for the law firm is 1475 Calloway Street, Suite 210, Houston, Texas 77041. Phone Number: 832-361-9027; Fax Number: 832-614-7359. The logo is uploaded to the project.

```html
<!DOCTYPE html>
<html lang="en">
<head>
<meta charset="utf-8">
<title>Marwick Law Letterhead</title>
<link rel="stylesheet" href="https://fonts.googleapis.com/css2?family=Montserrat:wght@400;600&family=Mrs+Saint+Delafield&display=swap">
<style>
  :root {
    --navy: #1b2f5e;
    --red: #e31b23;
    --ink: #222326;
    --paper: #ffffff;
    --backdrop: #e8e8e8;
  }
  * { margin: 0; padding: 0; box-sizing: border-box; }
  html, body {
    width: 1154px; height: 1200px; overflow: hidden;
    background: var(--backdrop);
  }
  .letterhead {
    position: absolute; left: 162px; top: 20px;
    width: 830px; height: 1160px;
    background: var(--paper);
    font-family: "Montserrat", sans-serif;
    color: var(--ink);
    overflow: hidden;
  }
  .firm-name {
    position: absolute; left: 32px; top: 100px;
    font-size: 32px; font-weight: 600; color: var(--navy);
    letter-spacing: 0.5px;
  }
  .contact { position: absolute; left: 32px; top: 196px; list-style: none; font-size: 13.5px; }
  .contact li { display: flex; align-items: center; height: 21px; }
  .contact svg { width: 11px; height: 11px; margin-right: 12px; fill: var(--red); }
  .recipient { position: absolute; left: 31px; top: 288px; font-size: 13.5px; line-height: 20.6px; }
  .body-copy { position: absolute; left: 33px; top: 377px; width: 768px; font-size: 13.4px; line-height: 20.6px; }
  .body-copy p { text-align: justify; margin-bottom: 20.6px; }
  .closing { position: absolute; left: 31px; top: 866px; font-size: 16px; }
  .signature {
    position: absolute; left: 30px; top: 888px;
    font-family: "Mrs Saint Delafield", cursive; font-size: 34px; color: var(--ink);
  }
  .footer-band { position: absolute; left: 0; top: 950px; width: 830px; height: 210px; }
  .address {
    position: absolute; left: 0; right: 0; top: 1108px;
    display: flex; justify-content: center; align-items: center;
    color: #fff; font-size: 14.6px;
  }
  .address svg { width: 16px; height: 22px; margin-right: 12px; fill: #fff; }
</style>
</head>
<body>
<main class="letterhead">
  <div class="firm-name">Marwick Law</div>

  <ul class="contact">
    <li><svg viewBox="0 0 24 24"><path d="M6.6 10.8a15.1 15.1 0 0 0 6.6 6.6l2.2-2.2c.3-.3.7-.4 1-.2 1.1.4 2.3.6 3.6.6.6 0 1 .4 1 1V20c0 .6-.4 1-1 1A17 17 0 0 1 3 4c0-.6.4-1 1-1h3.5c.6 0 1 .4 1 1 0 1.3.2 2.5.6 3.6.1.3 0 .7-.2 1z"/></svg>832-361-9027</li>
    <li><svg viewBox="0 0 24 24"><path d="M6 2h12v6H6zM3 9h18a1 1 0 0 1 1 1v7h-4v5H6v-5H2v-7a1 1 0 0 1 1-1zm5 7v4h8v-4z"/></svg>832-614-7359</li>
  </ul>

  <address class="recipient" style="font-style:normal">
    Mr/s<br>First Name and Last Name<br>Company Name<br>Address
  </address>

  <section class="body-copy">
    <p>Lorem ipsum dolor sit amet,consectetur adipiscing sed do eiusmod tempor incididunt laboreet dolore magna aliqua.Ut enim ad minim.veniam, quis nostrud exercitation ullamco laboris nisi ut aliquip exea commodo con-sequat.Lorem ipsum dolor sit amet,consectetur adipiscing sed do eiusmod tempor incididunt.labore et dolore magna aliqua. Ut enim</p>
    <p>Lorem ipsum dolor sit amet, consectetur adipiscing sed do eiusmod tempor incididunt labore et dolore magna aliqua. Ut enim ad minim veniam, quis nostrud exercitation ullamco laboris nisi ut aliquip exea commo-do consequat.Duis aute irure dolor in reprehenderit in voluptate velit esse cillum irure dolor in reprehenderit in voluptate velit esse irure</p>
    <p>Lorem ipsum dolor sit amet, consectetur adipiscing sed do eiusmod tempor incididunt labore et dolore magna aliqua. consequat. Duis aute irure dolor in.reprehenderit in voluptate velit esse cillum dolore eu fugiat nulla pariatur. Excepteur sint occaecat cupidatat non proident, sunt in culpa qui officia deserunt mollit,</p>
    <p>Lorem ipsum dolor sit amet, consectetur adipiscing sed do eiusmod tempor incididunt labore et dolore magna aliqua. Ut enim Lorem ipsum dolor sit amet, consectetur adipiscing sed do eiusmod tempor incididunt labore et dolore magna aliqua. Ut enim Lorem ipsum aliqua.ipsum</p>
    <p>Lorem ipsum dolor sit amet, consectetur adipiscing sed do eiusmod tempor incididunt labore et dolore magna aliqua. Ut enim ad minim veniam, quis nostrud exercitation ullamco laboris nisi ut aliquip exea commo-do consequat.Duis aute irure dolor in reprehenderit in voluptate velit esse cillum irure dolor in reprehenderit in voluptate velit esse irure</p>
  </section>

  <div class="closing">Regards</div>
  <div class="signature">Hallorans</div>

  <svg class="footer-band" viewBox="0 0 830 210" preserveAspectRatio="none" aria-hidden="true">
    <path d="M0 112 C250 126 600 102 830 42 L830 210 L0 210Z" fill="var(--navy)"/>
    <path d="M283 111 C500 102 700 62 830 9 L830 28 C700 76 500 108 283 111Z" fill="var(--red)"/>
  </svg>

  <div class="address">
    <svg viewBox="0 0 16 22"><path d="M8 0a8 8 0 0 0-8 8c0 6 8 14 8 14s8-8 8-14a8 8 0 0 0-8-8zm0 11a3 3 0 1 1 0-6 3 3 0 0 1 0 6z"/></svg>
    1475 Calloway Street, Suite 210, Houston, Texas 77041
  </div>
</main>
</body>
</html>
```